KorvaNest - Home Income and Business Resources Platform

I am looking for a website template for a multi-purposed website. This website will feature:

1.) Website Directory with Ratings & comments on listings
2.) Company Blog
3.) Homepage with Content (see files for homepage mock)

I would like the Design to have a default width 1170px (wider then normal)

Of course I am looking for Pages for Listings to be designed.

Great looking BLOG Layout: http://journal.plimworks.example/html/blog.html

I would like 4 Versions of a Website Directory Listing "Box"
1.) Basic Listing Box
2.) Sponsored Listing Box
3.) Recommended Listing Box
4.) Stay Away From Listing Box

Information on the Listing Page (Like on a Category Page)
Site Name, Site URL, Website Image, # of Views, Rating and # of Comments

Information on the Listing Details Page:
Same as ABOVE + About website Description, Vornic Score, Category Information

Decent looking examples is here: https://samples.trevolin.example/directory/computers/ and http://www.zqrankhub.example/.

I will include some sketches and screenshots of things I like/looking for. As designers,you have creative freedom and are encouraged to show this. This is Phase one of this project and winning designer is guaranteed to have future work for this project.

Target Market(s)

Directory, business, websites

Industry/Entity Type

Business

Coding

Coded - Design and coding required

Number of Pages Required

5+ page

Font styles to use
Sans Serif

Colors

Designer to choose colors to be used in the design.

Requirements
Must have
• Professional yet clean look. The use of Icons & images
• Unique Look
Should not have
• Any exact copies of any examples I provided

```html
<!DOCTYPE html>
<html lang="en">
<head>
<meta charset="utf-8">
<title>KorvaNest – Business Directory</title>
<link href="https://fonts.googleapis.com/css2?family=Lato:ital,wght@0,400;0,700;0,900;1,400&display=swap" rel="stylesheet">
<style>
:root{
  --orange:#f0862a;
  --ink:#2a2a2a;
  --text:#555;
  --muted:#777;
  --rule:#d9d9d9;
  --panel-dark:#5b5b5b;
  --star:#e8bf1a;
  --footer:#1f1f1f;
  --white:#fff;
}
*{box-sizing:border-box;margin:0;padding:0}
html,body{width:1200px;height:2225px;overflow:hidden}
body{font-family:"Lato",sans-serif;color:var(--text);background:var(--white);position:relative}
a{color:inherit;text-decoration:none}
ul{list-style:none}

/* Header */
.site-header{position:absolute;top:0;left:0;width:1200px;height:82px;border-top:3px solid var(--orange);background:var(--white);box-shadow:0 1px 3px rgba(0,0,0,.08);z-index:2}
.brand{position:absolute;left:98px;top:29px;font-size:22px;font-weight:900;color:var(--ink);letter-spacing:.3px}
.main-nav{position:absolute;top:33px;left:0;font-size:14.5px;font-weight:700;color:var(--ink);text-transform:uppercase}
.main-nav a{position:absolute;white-space:nowrap}
.main-nav a.is-active{color:var(--orange)}
.search-icon{position:absolute;left:986px;top:35px}
.login-btn{position:absolute;left:1020px;top:25px;width:81px;height:36px;border:1px solid #bdbdbd;color:var(--orange);font-weight:700;font-size:14.5px;display:flex;align-items:center;justify-content:center;gap:5px}

/* Hero */
.hero{position:absolute;top:82px;left:0;width:1200px;height:290px;background:linear-gradient(90deg,#e4e6e8 0%,#f2f3f4 35%,#eceff1 60%,#cfd6dc 100%);overflow:hidden}
.hero-photo{position:absolute;right:0;top:0;width:560px;height:290px;background:radial-gradient(ellipse at 55% 40%,#d9b8a4 0%,#c4a08c 25%,#9ba8b8 55%,#e7a9bc 80%,#e8e9eb 100%);opacity:.75}
.hero-title{position:absolute;left:100px;top:112px;font-size:48px;font-weight:900;color:var(--ink);letter-spacing:.2px}

/* Breadcrumb */
.breadcrumb{position:absolute;top:394px;left:98px;width:1002px;height:38px;border-bottom:1px solid var(--rule);font-size:16px;font-weight:700;color:#555}
.breadcrumb .current{color:var(--orange)}
.breadcrumb .sep{margin:0 6px}

/* Listings */
.listings{position:absolute;top:481px;left:98px;width:673px}
.section-title{font-size:25px;font-weight:900;color:var(--ink);height:65px}
.listing{position:relative;height:224px;border-bottom:1px solid var(--rule);margin-bottom:33px}
.listing-thumb{position:absolute;left:0;top:0;width:262px;height:191px;border:1px solid #d4d4d4;box-shadow:0 1px 4px rgba(0,0,0,.15);padding:4px;background:var(--white)}
.listing-thumb div{width:100%;height:100%}
.listing-body{position:absolute;left:290px;top:0;width:383px}
.listing-name{font-size:22px;font-weight:700;color:var(--ink);line-height:28px}
.listing-url{margin-top:8px;font-size:14.5px;font-style:italic;color:#444;display:flex;align-items:center;gap:8px}
.listing-desc{margin-top:16px;font-size:12.6px;line-height:23.5px;color:#666}
.listing-meta{margin-top:18px;font-size:13px;color:#666;display:flex;align-items:center;gap:6px}
.stars{display:flex;gap:1px}
.listing-meta .bar{margin:0 5px}
.meta-item{display:flex;align-items:center;gap:3px}
.view-more{position:absolute;top:2086px;left:98px;font-size:14px;font-weight:900;color:var(--orange)}

/* Sidebar */
.sidebar-box{position:absolute;left:854px;width:246px;border:1px solid #d6d6d6;box-shadow:0 1px 3px rgba(0,0,0,.1);background:var(--white)}
.sidebar-box h3{margin:3px 3px 0;height:40px;line-height:40px;padding-left:24px;font-size:17.5px;font-weight:900;color:var(--white);text-transform:uppercase}
.sidebar-box h3.accent{background:var(--orange)}
.sidebar-box h3.dark{background:var(--panel-dark)}
.sidebar-box ul{padding-left:27px;font-size:12.5px;color:#555}
.sidebar-box li{display:flex;align-items:center;gap:10px}
.sidebar-box li.is-active{color:var(--orange)}
.ranking{top:485px;height:135px}
.ranking ul{padding-top:15px}
.ranking li{height:29px}
.directory{top:648px;height:280px}
.directory ul{padding-top:25px}
.directory li{height:36px}
.categories{top:956px;height:522px}
.categories ul{padding-top:24px}
.categories li{height:25.8px}

/* Footer */
.site-footer{position:absolute;left:0;top:2156px;width:1200px;height:69px;background:var(--footer);color:#e5e5e5;font-size:12px;text-align:center;line-height:69px}
</style>
</head>
<body>
<svg width="0" height="0" style="position:absolute">
  <defs>
    <symbol id="star" viewBox="0 0 24 24"><path d="M12 2l2.9 6.9 7.1.6-5.4 4.7 1.6 7-6.2-3.8-6.2 3.8 1.6-7L2 9.5l7.1-.6z"/></symbol>
    <symbol id="tick" viewBox="0 0 12 12"><circle cx="6" cy="6" r="6" fill="#f0862a"/><path d="M3.2 6.2l1.9 1.9 3.7-3.8" fill="none" stroke="#fff" stroke-width="1.6"/></symbol>
    <symbol id="globe" viewBox="0 0 12 12"><circle cx="6" cy="6" r="6" fill="#f0862a"/><path d="M1 6h10M6 1c2.5 2.8 2.5 7.2 0 10M6 1c-2.5 2.8-2.5 7.2 0 10" fill="none" stroke="#fff" stroke-width=".9"/></symbol>
    <symbol id="eye" viewBox="0 0 16 10"><path d="M1 5c2-3 4-4 7-4s5 1 7 4c-2 3-4 4-7 4S3 8 1 5z" fill="none" stroke="#f0862a" stroke-width="1.5"/><circle cx="8" cy="5" r="2" fill="#f0862a"/></symbol>
    <symbol id="comment" viewBox="0 0 16 14"><path d="M2 2h10a2 2 0 012 2v4a2 2 0 01-2 2H7l-3 3v-3H2a2 2 0 01-2-2V4a2 2 0 012-2z" fill="none" stroke="#f0862a" stroke-width="1.5"/></symbol>
  </defs>
</svg>

<header class="site-header">
  <a class="brand" href="#">KORVANEST</a>
  <nav class="main-nav">
    <a style="left:329px" href="#">Home</a>
    <a style="left:406px" href="#">About Us</a>
    <a style="left:510px" href="#">Resources</a>
    <a style="left:626px" class="is-active" href="#">Business Directory</a>
    <a style="left:811px" href="#">News</a>
    <a style="left:885px" href="#">Contact</a>
  </nav>
  <svg class="search-icon" width="14" height="14" viewBox="0 0 14 14" aria-label="Search"><circle cx="6" cy="6" r="4.5" fill="none" stroke="#2a2a2a" stroke-width="2"/><path d="M9.3 9.3l3.5 3.5" stroke="#2a2a2a" stroke-width="2.2"/></svg>
  <a class="login-btn" href="#"><svg width="11" height="13" viewBox="0 0 11 13"><rect x="0" y="5.5" width="11" height="7.5" rx="1" fill="#f0862a"/><path d="M2.5 5.5V4a3 3 0 016 0v1.5" fill="none" stroke="#f0862a" stroke-width="1.6"/></svg>LOGIN</a>
</header>

<section class="hero">
  <div class="hero-photo" role="img" aria-label="Photo of a smiling couple looking at a laptop together"></div>
  <h1 class="hero-title">BUSINESS DIRECTORY</h1>
</section>

<div class="breadcrumb"><a href="#">HOME</a><span class="sep">&gt;&gt;</span><span class="current">BUSINESS DIRECTORY</span></div>

<main class="listings">
  <h2 class="section-title">TOP LISTINGS</h2>

  <article class="listing">
    <div class="listing-thumb"><div role="img" aria-label="Website screenshot with teal header and white content area" style="background:linear-gradient(180deg,#d8dde0 0 6%,#3bb3c3 6% 40%,#eef1f2 40%)"></div></div>
    <div class="listing-body">
      <h3 class="listing-name">Finibus Bonorum</h3>
      <p class="listing-url"><svg width="12" height="12"><use href="#globe"/></svg>https://samples.finibus.example/directory/</p>
      <p class="listing-desc">Nam libero tempore, cum soluta nobis est eligendi optio cumquenih il impedit quo minus id quod maxime placeat facere possimus, onis voluptas assumenda est, omnis dolor repellendus.</p>
      <div class="listing-meta"><span class="stars"><svg width="15" height="15" fill="#e8bf1a"><use href="#star"/></svg><svg width="15" height="15" fill="#e8bf1a"><use href="#star"/></svg><svg width="15" height="15" fill="#e8bf1a"><use href="#star"/></svg><svg width="15" height="15" fill="#e8bf1a"><use href="#star"/></svg><svg width="15" height="15" fill="none" stroke="#e8bf1a" stroke-width="2"><use href="#star"/></svg></span>(7 Ratings)<span class="bar">|</span><span class="meta-item"><svg width="12" height="8"><use href="#eye"/></svg>25 Views</span><span class="bar">|</span><span class="meta-item"><svg width="12" height="11"><use href="#comment"/></svg>0 Comments</span></div>
    </div>
  </article>

  <article class="listing">
    <div class="listing-thumb"><div role="img" aria-label="Website screenshot with blue swirl banner" style="background:linear-gradient(180deg,#1f8fc4 0 6%,#e5f2f8 6% 22%,#2ba7d6 22% 55%,#148ac2 55%)"></div></div>
    <div class="listing-body">
      <h3 class="listing-name">Finibus Bonorum</h3>
      <p class="listing-url"><svg width="12" height="12"><use href="#globe"/></svg>https://samples.finibus.example/directory/</p>
      <p class="listing-desc">Nam libero tempore, cum soluta nobis est eligendi optio cumquenih il impedit quo minus id quod maxime placeat facere possimus, onis voluptas assumenda est, omnis dolor repellendus.</p>
      <div class="listing-meta"><span class="stars"><svg width="15" height="15" fill="#e8bf1a"><use href="#star"/></svg><svg width="15" height="15" fill="#e8bf1a"><use href="#star"/></svg><svg width="15" height="15" fill="#e8bf1a"><use href="#star"/></svg><svg width="15" height="15" fill="#e8bf1a"><use href="#star"/></svg><svg width="15" height="15" fill="none" stroke="#e8bf1a" stroke-width="2"><use href="#star"/></svg></span>(7 Ratings)<span class="bar">|</span><span class="meta-item"><svg width="12" height="8"><use href="#eye"/></svg>25 Views</span><span class="bar">|</span><span class="meta-item"><svg width="12" height="11"><use href="#comment"/></svg>0 Comments</span></div>
    </div>
  </article>

  <article class="listing">
    <div class="listing-thumb"><div role="img" aria-label="Website screenshot with green header" style="background:linear-gradient(180deg,#f2f4ee 0 8%,#6aa33a 8% 30%,#f4f5f2 30%)"></div></div>
    <div class="listing-body">
      <h3 class="listing-name">Finibus Bonorum</h3>
      <p class="listing-url"><svg width="12" height="12"><use href="#globe"/></svg>https://samples.finibus.example/directory/</p>
      <p class="listing-desc">Nam libero tempore, cum soluta nobis est eligendi optio cumquenih il impedit quo minus id quod maxime placeat facere possimus, onis voluptas assumenda est, omnis dolor repellendus.</p>
      <div class="listing-meta"><span class="stars"><svg width="15" height="15" fill="#e8bf1a"><use href="#star"/></svg><svg width="15" height="15" fill="#e8bf1a"><use href="#star"/></svg><svg width="15" height="15" fill="#e8bf1a"><use href="#star"/></svg><svg width="15" height="15" fill="#e8bf1a"><use href="#star"/></svg><svg width="15" height="15" fill="none" stroke="#e8bf1a" stroke-width="2"><use href="#star"/></svg></span>(7 Ratings)<span class="bar">|</span><span class="meta-item"><svg width="12" height="8"><use href="#eye"/></svg>25 Views</span><span class="bar">|</span><span class="meta-item"><svg width="12" height="11"><use href="#comment"/></svg>0 Comments</span></div>
    </div>
  </article>

  <article class="listing">
    <div class="listing-thumb"><div role="img" aria-label="Website screenshot with orange print shop banner" style="background:linear-gradient(180deg,#f6f6f6 0 30%,#f39a1e 30% 90%,#e57e12 90%)"></div></div>
    <div class="listing-body">
      <h3 class="listing-name">Finibus Bonorum</h3>
      <p class="listing-url"><svg width="12" height="12"><use href="#globe"/></svg>https://samples.finibus.example/directory/</p>
      <p class="listing-desc">Nam libero tempore, cum soluta nobis est eligendi optio cumquenih il impedit quo minus id quod maxime placeat facere possimus, onis voluptas assumenda est, omnis dolor repellendus.</p>
      <div class="listing-meta"><span class="stars"><svg width="15" height="15" fill="#e8bf1a"><use href="#star"/></svg><svg width="15" height="15" fill="#e8bf1a"><use href="#star"/></svg><svg width="15" height="15" fill="#e8bf1a"><use href="#star"/></svg><svg width="15" height="15" fill="#e8bf1a"><use href="#star"/></svg><svg width="15" height="15" fill="none" stroke="#e8bf1a" stroke-width="2"><use href="#star"/></svg></span>(7 Ratings)<span class="bar">|</span><span class="meta-item"><svg width="12" height="8"><use href="#eye"/></svg>25 Views</span><span class="bar">|</span><span class="meta-item"><svg width="12" height="11"><use href="#comment"/></svg>0 Comments</span></div>
    </div>
  </article>

  <article class="listing">
    <div class="listing-thumb"><div role="img" aria-label="Website screenshot with beach travel banner" style="background:linear-gradient(180deg,#1e2a44 0 6%,#7fb3d8 6% 35%,#d8c6a0 35% 78%,#f5f5f5 78%)"></div></div>
    <div class="listing-body">
      <h3 class="listing-name">Finibus Bonorum</h3>
      <p class="listing-url"><svg width="12" height="12"><use href="#globe"/></svg>https://samples.finibus.example/directory/</p>
      <p class="listing-desc">Nam libero tempore, cum soluta nobis est eligendi optio cumquenih il impedit quo minus id quod maxime placeat facere possimus, onis voluptas assumenda est, omnis dolor repellendus.</p>
      <div class="listing-meta"><span class="stars"><svg width="15" height="15" fill="#e8bf1a"><use href="#star"/></svg><svg width="15" height="15" fill="#e8bf1a"><use href="#star"/></svg><svg width="15" height="15" fill="#e8bf1a"><use href="#star"/></svg><svg width="15" height="15" fill="#e8bf1a"><use href="#star"/></svg><svg width="15" height="15" fill="none" stroke="#e8bf1a" stroke-width="2"><use href="#star"/></svg></span>(7 Ratings)<span class="bar">|</span><span class="meta-item"><svg width="12" height="8"><use href="#eye"/></svg>25 Views</span><span class="bar">|</span><span class="meta-item"><svg width="12" height="11"><use href="#comment"/></svg>0 Comments</span></div>
    </div>
  </article>

  <article class="listing">
    <div class="listing-thumb"><div role="img" aria-label="Website screenshot of an admin dashboard with colored tiles" style="background:linear-gradient(180deg,#3c8dbc 0 5%,#eef1f4 5% 12%,#d9e6ef 12% 30%,#f4f6f8 30% 78%,#5cc8d0 78%)"></div></div>
    <div class="listing-body">
      <h3 class="listing-name">Finibus Bonorum</h3>
      <p class="listing-url"><svg width="12" height="12"><use href="#globe"/></svg>https://samples.finibus.example/directory/</p>
      <p class="listing-desc">Nam libero tempore, cum soluta nobis est eligendi optio cumquenih il impedit quo minus id quod maxime placeat facere possimus, onis voluptas assumenda est, omnis dolor repellendus.</p>
      <div class="listing-meta"><span class="stars"><svg width="15" height="15" fill="#e8bf1a"><use href="#star"/></svg><svg width="15" height="15" fill="#e8bf1a"><use href="#star"/></svg><svg width="15" height="15" fill="#e8bf1a"><use href="#star"/></svg><svg width="15" height="15" fill="#e8bf1a"><use href="#star"/></svg><svg width="15" height="15" fill="none" stroke="#e8bf1a" stroke-width="2"><use href="#star"/></svg></span>(7 Ratings)<span class="bar">|</span><span class="meta-item"><svg width="12" height="8"><use href="#eye"/></svg>25 Views</span><span class="bar">|</span><span class="meta-item"><svg width="12" height="11"><use href="#comment"/></svg>0 Comments</span></div>
    </div>
  </article>
</main>
<a class="view-more" href="#">VIEW MORE &gt;&gt;</a>

<aside>
  <section class="sidebar-box ranking">
    <h3 class="accent">Ranking Method</h3>
    <ul>
      <li><svg width="12" height="12"><use href="#tick"/></svg>Rank By Hits In</li>
      <li><svg width="12" height="12"><use href="#tick"/></svg>Rank By Hits Out</li>
    </ul>
  </section>
  <section class="sidebar-box directory">
    <h3 class="dark">Directory</h3>
    <ul>
      <li><svg width="12" height="12"><use href="#tick"/></svg>Add Listing</li>
      <li><svg width="12" height="12"><use href="#tick"/></svg>New Listings</li>
      <li class="is-active"><svg width="12" height="12"><use href="#tick"/></svg>Top Listings</li>
      <li><svg width="12" height="12"><use href="#tick"/></svg>Popular Listings</li>
      <li><svg width="12" height="12"><use href="#tick"/></svg>Random Listings</li>
    </ul>
  </section>
  <section class="sidebar-box categories">
    <h3 class="dark">Top Categories</h3>
    <ul>
      <li><svg width="12" height="12"><use href="#tick"/></svg>Arts 0</li>
      <li><svg width="12" height="12"><use href="#tick"/></svg>Business 7</li>
      <li><svg width="12" height="12"><use href="#tick"/></svg>Computers 8</li>
      <li><svg width="12" height="12"><use href="#tick"/></svg>Games 0</li>
      <li><svg width="12" height="12"><use href="#tick"/></svg>Health 0</li>
      <li><svg width="12" height="12"><use href="#tick"/></svg>Home 0</li>
      <li><svg width="12" height="12"><use href="#tick"/></svg>Kids and Teens 0</li>
      <li><svg width="12" height="12"><use href="#tick"/></svg>Misc 0</li>
      <li><svg width="12" height="12"><use href="#tick"/></svg>News 0</li>
      <li><svg width="12" height="12"><use href="#tick"/></svg>Recreation 0</li>
      <li><svg width="12" height="12"><use href="#tick"/></svg>Reference 0</li>
      <li><svg width="12" height="12"><use href="#tick"/></svg>Regional 0</li>
      <li><svg width="12" height="12"><use href="#tick"/></svg>Science 0</li>
      <li><svg width="12" height="12"><use href="#tick"/></svg>Shopping 0</li>
      <li><svg width="12" height="12"><use href="#tick"/></svg>Society 0</li>
      <li><svg width="12" height="12"><use href="#tick"/></svg>Sports 3</li>
    </ul>
  </section>
</aside>

<footer class="site-footer">Copyright © 2017. KorvaNest. All Rights Reserved.</footer>
</body>
</html>
```